Web Design for Independent Pet Supply shop.

Larch Critter Depot is a locally owned and operated premium natural pet food store and supply company with 2 thriving retail stores in Bend, Oregon, and a home delivery service. The pet food offered is the best on the market and may be described as “holistic”. Also on offer is a vast selection of toys, training tools, treats, and other supplies, as well as dog washing services that range from "do-it yourself" to "spa." Current site: LarchCritterDepot.com. They need a new, updated and responsive site.
Likes:
Tovanels.com: Natural colors, not loud, pages in motion, simple & clean but very informative.
Dorvikmerin.com: Everything in simple big colorful blocks. The specials run across the top and in motion. This site looks very professional but simple. The information is available several different places.
Plenharvest.com: Again big blocks through out. Very Fun and inviting. Tons of information with videos and recipes and testimonials. Pleasant feel and colors as well.
Dislikes:
Furlix.com: Looks cheap, hate the colors, very busy and over whelming. Hate the old style header bar going across with options. Too many printed words instead of fun images.
Colors should be "natural" tones, warm and soothing. Deep dark blue and greys with earthy wood color.
Do Not Use: Blue violet, violet, red violet

```html
<!DOCTYPE html>
<html lang="en">
<head>
<meta charset="utf-8">
<title>Larch Critter Depot</title>
<link href="https://fonts.googleapis.com/css2?family=Open+Sans:wdth,wght@75..100,300..800&display=swap" rel="stylesheet">
<style>
:root{
  --navy:#1c2462;
  --navy-deep:#161d55;
  --wood:#b07a2c;
  --wood-light:#d9b65a;
  --cream:#ebe3cf;
  --cream-dark:#e2d8bf;
  --mist:#f0efed;
  --text:#4a4a48;
  --muted:#8a8a86;
  --footer:#2b2b2b;
  --footer-deep:#161616;
  --line:#6a6a6a;
}
*{margin:0;padding:0;box-sizing:border-box}
html,body{width:1200px;height:2387px;overflow:hidden}
body{position:relative;font-family:"Open Sans",Arial,sans-serif;color:var(--text);background:var(--cream)}
.abs{position:absolute}
.cond{font-stretch:75%;font-weight:700}

/* header */
.site-header{left:0;top:0;width:1200px;height:113px;background:linear-gradient(180deg,#ede6d3,#e6dcc4)}
.brand{left:97px;top:40px;display:flex;align-items:center;gap:10px}
.brand-dot{width:26px;height:26px;border-radius:50%;background:var(--wood)}
.brand-name{font-size:24px;font-weight:700;color:var(--wood);font-stretch:75%;letter-spacing:.3px}
.main-nav{left:425px;top:45px;display:flex;font-size:13px;color:var(--navy)}
.main-nav a{color:var(--navy);text-decoration:none;margin-right:27px}
.main-nav a.current{color:var(--wood);position:relative}
.main-nav a.current::after{content:"";position:absolute;left:-4px;right:-4px;top:26px;height:1px;background:var(--wood)}
.search{left:1085px;top:52px}

/* hero */
.hero{left:0;top:113px;width:1200px;height:498px;background:linear-gradient(100deg,#6f7a38 0%,#a86a2c 25%,#c9842f 40%,#8c6a34 60%,#6d7e3a 80%,#55652e 100%)}
.hero-title{left:377px;top:225px;font-size:37px;line-height:44px;color:#fff;font-weight:800;font-stretch:85%;text-shadow:0 2px 4px rgba(0,0,0,.45)}
.hero-product{left:900px;top:100px;width:195px;height:298px;border-radius:4px;background:linear-gradient(180deg,#f2c520 0%,#f2c520 40%,#1f3e8c 40%,#1a357a 100%)}
.hero-arrow{top:195px}

/* welcome */
.welcome{left:0;top:611px;width:1200px;height:472px;background:var(--cream)}
.section-title{font-size:31px;color:var(--navy);font-stretch:75%;font-weight:700;text-align:center;width:1200px;left:0}
.intro{left:140px;top:92px;width:920px;text-align:center;font-size:12px;line-height:22px}
.divider{left:575px;width:50px;height:10px}
.feature{width:290px}
.feature-icon{width:62px;height:62px;border-radius:50%;background:var(--cream-dark);display:flex;align-items:center;justify-content:center}
.feature-title{left:80px;top:18px;font-size:17px;color:var(--navy);font-weight:600;line-height:24px;white-space:nowrap}
.feature-text{left:0;top:75px;width:285px;font-size:12px;line-height:22px}
.read-more{font-size:12.5px;color:var(--navy);display:flex;align-items:center;gap:7px}
.read-more.faint{color:#d4c9ae}
.read-more svg{display:block}

/* dog wash */
.dog-wash{left:0;top:1083px;width:1200px;height:385px;background:var(--mist)}
.dog-wash h2{left:97px;top:35px;font-size:29px;color:var(--navy)}
.wash-list{left:105px;top:101px;list-style:none;font-size:12px;line-height:26px;width:470px}
.wash-list li{position:relative;padding-left:22px}
.wash-list li::before{content:"";position:absolute;left:0;top:9px;width:8px;height:8px;border:1.5px solid var(--wood);border-radius:50%}
.dog-photo{left:610px;top:20px;width:590px;height:345px;border-radius:48% 40% 10% 30%/70% 60% 10% 20%;background:radial-gradient(ellipse at 45% 45%,#e8c99b,#d9b07a 50%,rgba(240,239,237,0) 72%)}

/* blog */
.blog{left:0;top:1468px;width:1200px;height:436px;background:var(--cream)}
.post-photo{width:252px;height:252px}
.post-date{width:85px;height:35px;background:var(--navy);color:#fff;font-size:13px;display:flex;align-items:center;justify-content:center}
.post-title{font-size:17px;line-height:23px;color:#555;width:240px;font-weight:400}
.post-text{font-size:12px;line-height:22px;width:205px}

/* newsletter */
.newsletter{left:0;top:1904px;width:1200px;height:101px;background:var(--mist)}
.news-head{left:243px;top:24px;font-size:16px;color:#555;letter-spacing:.3px}
.news-sub{left:243px;top:52px;font-size:16px;color:#aaa}
.news-input{left:624px;top:31px;width:326px;height:43px;background:#fff;border:1px solid #ddd;font-size:12px;color:#777;padding:13px 15px}
.news-btn{left:950px;top:31px;width:127px;height:43px;background:#666;color:#fff;font-size:15px;display:flex;align-items:center;justify-content:center}

/* footer */
.site-footer{left:0;top:2005px;width:1200px;height:319px;background:var(--footer);color:#fff}
.foot-title{font-size:17px;color:#fff;font-weight:600}
.field{left:124px;width:240px;height:41px;border:1px solid var(--line);font-size:11px;color:#888;padding:12px 14px}
.submit{left:124px;top:2243px;width:78px;height:37px;background:var(--navy-deep);color:#fff;font-size:13px;font-weight:600;display:flex;align-items:center;justify-content:center}
.fb-box{left:425px;top:2055px;width:190px;height:162px;background:#fff;color:#333}
.fb-cover{left:0;top:0;width:190px;height:80px;background:linear-gradient(180deg,#2f5b7a,#4c7f98 60%,#6a8f5a)}
.fb-name{left:10px;top:12px;font-size:14px;color:#fff}
.fb-likes{left:10px;top:32px;font-size:10px;color:#fff}
.fb-btn{left:8px;top:83px;width:78px;height:18px;border:1px solid #ccc;background:#f5f6f7;font-size:10px;display:flex;align-items:center;justify-content:center;color:#444}
.fb-note{left:14px;top:115px;font-size:10px;line-height:13px;width:160px;color:#555}
.fb-faces{left:14px;top:140px;display:flex;gap:4px}
.fb-faces span{width:20px;height:20px;background:#b9a58c}
.tweet{left:677px;width:215px;font-size:11px;line-height:21px;font-style:italic;color:#fff}
.tweet .ago{color:#ccc}
.policies{left:959px;top:2087px;list-style:none;font-size:11.5px;line-height:24px;color:#fff}
.policies li::before{content:"› "}
.bottom-bar{left:0;top:2324px;width:1200px;height:63px;background:var(--footer-deep)}
.copyright{left:97px;top:24px;font-size:11.5px;color:#ddd}
.socials{left:970px;top:16px;display:flex;gap:6px}
.socials span{width:27px;height:27px;border:1.5px solid #fff;border-radius:50%}
</style>
</head>
<body>

<header class="site-header abs">
  <div class="brand abs"><span class="brand-dot"></span><span class="brand-name">Larch Critter Depot</span></div>
  <nav class="main-nav abs">
    <a class="current">Home</a><a>Events</a><a>Blog</a><a>About</a><a>Dog Wash</a><a>Products</a><a>Resources</a><a>Links</a><a>Contact</a>
  </nav>
  <svg class="search abs" width="18" height="18" viewBox="0 0 18 18"><circle cx="7.5" cy="7.5" r="5.5" fill="none" stroke="#b07a2c" stroke-width="2.5"/><line x1="11.5" y1="11.5" x2="16" y2="16" stroke="#b07a2c" stroke-width="3"/></svg>
</header>

<section class="hero abs" role="img" aria-label="Golden retriever lying on a forest path">
  <div class="hero-product abs" role="img" aria-label="Bag of large breed dog food"></div>
  <h1 class="hero-title abs">DEDICATED TO A BETTER DIET<br>FOR A HEALTHIER PET</h1>
  <svg class="hero-arrow abs" style="left:40px" width="18" height="110" viewBox="0 0 18 110"><polyline points="16,2 2,55 16,108" fill="none" stroke="#fff" stroke-width="1.5" opacity=".8"/></svg>
  <svg class="hero-arrow abs" style="left:1142px" width="18" height="110" viewBox="0 0 18 110"><polyline points="2,2 16,55 2,108" fill="none" stroke="#fff" stroke-width="1.5" opacity=".8"/></svg>
</section>

<section class="welcome abs">
  <h2 class="section-title abs cond" style="top:45px">Welcome to Larch Critter Depot</h2>
  <p class="intro abs">The Larch Critter Depot Dog Wash attendants are always here to help wash your four-legged friends, and trim their nails...but they are also here to help educate all of us! Nail trims are such an essential routine for our pups, especially if they don't run and walk as much as they would in the wild.</p>
  <svg class="divider abs" style="top:155px" viewBox="0 0 50 10"><line x1="0" y1="5" x2="19" y2="5" stroke="#b07a2c"/><circle cx="25" cy="5" r="4" fill="none" stroke="#b07a2c"/><line x1="31" y1="5" x2="50" y2="5" stroke="#b07a2c"/></svg>

  <article class="feature abs" style="left:124px;top:186px">
    <div class="feature-icon"><svg width="26" height="26" viewBox="0 0 24 24"><polygon points="12,2 15,9 22,9.5 16.5,14 18.5,21 12,17 5.5,21 7.5,14 2,9.5 9,9" fill="#e8c020" stroke="#b07a2c"/></svg></div>
    <h3 class="feature-title abs">Pup Brew</h3>
    <p class="feature-text abs">Now you can pour some cold brew for your pup in a fun and easy way that has a delicious flavor and packed full of vegetarian K9 specific glucosamine with essential vitamins and minerals for your dogs health and well being.</p>
    <div class="read-more faint abs" style="top:190px">Read more <svg width="10" height="10"><circle cx="5" cy="5" r="4" fill="none" stroke="#d4c9ae"/></svg></div>
  </article>

  <article class="feature abs" style="left:458px;top:186px">
    <div class="feature-icon"><svg width="24" height="26" viewBox="0 0 24 26"><line x1="5" y1="3" x2="5" y2="24" stroke="#b07a2c" stroke-width="2"/><path d="M6 4 H20 L17 9 L20 14 H6Z" fill="#e8c020" stroke="#b07a2c"/></svg></div>
    <h3 class="feature-title abs">Purvale Lawsuit</h3>
    <p class="feature-text abs">IN NEWS: Purvale is being sued by , Dale Morrow of Cedar Bay, California. He he first purchased Happitail food in December or January. Since, he has witnessed one of his dogs pass away and 2 of his dogs get sick. PLEASE read and watch this link for more information!</p>
    <div class="read-more faint abs" style="top:212px">Read more <svg width="10" height="10"><circle cx="5" cy="5" r="4" fill="none" stroke="#d4c9ae"/></svg></div>
  </article>

  <article class="feature abs" style="left:792px;top:186px">
    <div class="feature-icon"><svg width="26" height="26" viewBox="0 0 24 24"><polygon points="12,2 15,9 22,9.5 16.5,14 18.5,21 12,17 5.5,21 7.5,14 2,9.5 9,9" fill="#e8c020" stroke="#b07a2c"/></svg></div>
    <h3 class="feature-title abs" style="top:8px">Tidecraft 5/8" Leads<br>On Sale</h3>
    <p class="feature-text abs">Your local Tidecraft has ALL of their 5/8" Leads ON SALE for just $10!</p>
    <div class="read-more faint abs" style="top:124px">Read more <svg width="10" height="10"><circle cx="5" cy="5" r="4" fill="none" stroke="#d4c9ae"/></svg></div>
  </article>
</section>

<section class="dog-wash abs">
  <div class="dog-photo abs" role="img" aria-label="Golden retriever lying with three puppies"></div>
  <h2 class="abs cond">The Larch Critter Depot Dog Wash</h2>
  <ul class="wash-list abs">
    <li>The 'Before' shot shows the dogs two front feet.</li>
    <li>Notice the two outside toes twisting out and away from the foot.</li>
    <li>The right foot ( Dogs left foot ) has already been trimmed.</li>
    <li>Dog toe/foot pads relay information to the dog like where the ground is, what angle the slope/stairs are, etc.</li>
    <li>When toes get twisted due to long nails, signals get mixed and dogs start trying to compensate by standing differently resulting in more strain in their skeletal structure.</li>
  </ul>
  <div class="read-more abs" style="left:123px;top:322px">Read more <svg width="11" height="11"><circle cx="5.5" cy="5.5" r="4.5" fill="none" stroke="#b07a2c"/><polyline points="4,3.5 6.5,5.5 4,7.5" fill="none" stroke="#b07a2c"/></svg></div>
</section>

<section class="blog abs">
  <h2 class="section-title abs cond" style="top:50px">Our Latest blog</h2>
  <svg class="divider abs" style="top:100px" viewBox="0 0 50 10"><line x1="0" y1="5" x2="19" y2="5" stroke="#b07a2c"/><circle cx="25" cy="5" r="4" fill="none" stroke="#b07a2c"/><line x1="31" y1="5" x2="50" y2="5" stroke="#b07a2c"/></svg>

  <div class="post-photo abs" style="left:99px;top:122px;background:linear-gradient(135deg,#d9b49a,#f1ebe2 50%,#cfa487)" role="img" aria-label="Couple hugging a labrador"></div>
  <div class="post-date abs" style="left:350px;top:139px">Nov 26</div>
  <h3 class="post-title abs" style="left:370px;top:202px">The Larch Critter Depot Dog Wash</h3>
  <p class="post-text abs" style="left:370px;top:254px">The Larch Critter Depot Dog Wash attendants are always here to help wash your four-legged friends, and trim their nails...</p>
  <div class="read-more abs" style="left:370px;top:352px">Read more <svg width="11" height="11"><circle cx="5.5" cy="5.5" r="4.5" fill="none" stroke="#b07a2c"/><polyline points="4,3.5 6.5,5.5 4,7.5" fill="none" stroke="#b07a2c"/></svg></div>

  <div class="post-photo abs" style="left:600px;top:122px;background:linear-gradient(160deg,#c8d66a,#6f9a35 45%,#3f6d24)" role="img" aria-label="Child and dog sitting on grass"></div>
  <div class="post-date abs" style="left:852px;top:139px">Nov 26</div>
  <h3 class="post-title abs" style="left:872px;top:202px">The Larch Critter Depot Dog Wash</h3>
  <p class="post-text abs" style="left:872px;top:254px">The Larch Critter Depot Dog Wash attendants are always here to help wash your four-legged friends, and trim their nails...</p>
  <div class="read-more abs" style="left:872px;top:352px">Read more <svg width="11" height="11"><circle cx="5.5" cy="5.5" r="4.5" fill="none" stroke="#b07a2c"/><polyline points="4,3.5 6.5,5.5 4,7.5" fill="none" stroke="#b07a2c"/></svg></div>
</section>

<section class="newsletter abs">
  <svg class="abs" style="left:118px;top:18px" width="100" height="80" viewBox="0 0 100 80"><g transform="rotate(-22 50 40)" fill="none" stroke="#dcdcda" stroke-width="3"><rect x="15" y="15" width="70" height="50" rx="3"/><polyline points="15,15 50,45 85,15"/></g></svg>
  <div class="news-head abs">JOIN OUR NEWSLETTER</div>
  <div class="news-sub abs">Lorem ipsum dolor sit amet, consectetur</div>
  <div class="news-input abs">Enter your E - mail</div>
  <div class="news-btn abs">SUBSCRIBE</div>
</section>

<footer class="site-footer abs">
  <h4 class="foot-title abs" style="left:124px;top:36px">Contact Form</h4>
  <h4 class="foot-title abs" style="left:677px;top:36px">Recent Tweets</h4>
  <h4 class="foot-title abs" style="left:959px;top:36px">Policies</h4>
</footer>
<div class="field abs" style="top:2089px">Name</div>
<div class="field abs" style="top:2140px">Phone Number</div>
<div class="field abs" style="top:2191px">Email</div>
<div class="submit abs">Submit</div>

<div class="fb-box abs">
  <div class="fb-cover abs" role="img" aria-label="Page cover photo of a lake"></div>
  <div class="fb-name abs">Larch Critter De...</div>
  <div class="fb-likes abs">1.6k likes</div>
  <div class="fb-btn abs">Like Page</div>
  <p class="fb-note abs">Be the first of your friends to like this</p>
  <div class="fb-faces abs"><span></span><span></span><span></span><span></span></div>
</div>

<div class="tweet abs" style="top:2090px">@mTinker The link to the SitePress version of Meadow Shop is in my previous tweet<br><span class="ago">6 months ago</span></div>
<div class="tweet abs" style="top:2185px">The SitePress version of Meadow Shop is now available: http://lnk.ex/R8dQp2<br><span class="ago">6 months ago</span></div>

<ul class="policies abs"><li>Contact</li><li>Return Policy</li><li>Privacy Policy</li><li>Employment</li><li>Staff Login</li></ul>

<div class="bottom-bar abs">
  <div class="copyright abs">Copyright © 2015 Larch Critter Depot Term of Use</div>
  <div class="socials abs"><span></span><span></span><span></span><span></span></div>
</div>

</body>
</html>
```